We are looking for a new PowerPoint template for our new CI

Hey pixelforum! For 25 years we have been an owner-managed IT system house with tradition, values and a great team. After more than 10 years, we would like to upgrade our company and design the entire CI contemporary and modern. Therefore we are looking for a Powerpoint Template which fits to our logo, the colors and an IT company. Details about our company and our service portfolio can be found on our homepage. We are currently adapting our homepage to the new CI resulting from the logo revision. Homepage: http://stage.rovalnet.example Color codes: Gray = RGB: 4040404040 White = RGB: F5F5F5F5F5 Orange = RGB: F7931E Our slogan: We keep your system running Our address data: Company = Kelmar Systeme GmbH Street = Birkenhang 12 POSTCODE = 61847 City = Burladingen We look forward to your ideas and thank you all in advance.

Target Market(s)

Our target group are companies with 10 to 100 employees from all industrial sectors, eg https://www.fernwald-logistik.example/ https://www.mauler-spedition.example/ https://www.quendt.example/ de /

Colors

Designer to choose colors to be used in the design.

Requirements
Must have
• We are looking for a modern IT design in gray / orange. The basis of the design should be our logo. The template should have two different layouts and three different layouts for content. Our logo and slogan should be clearly visible on the start layout. In addition, an area should be reserved for the name of a speaker and the occasion of the presentation.

```html
<!DOCTYPE html>
<html lang="de">
<head>
<meta charset="utf-8">
<title>Professionelles IT Management</title>
<link rel="stylesheet" href="https://fonts.googleapis.com/css2?family=Open+Sans:wght@400&display=swap">
<style>
  :root {
    --orange: #F7931E;
    --text-gray: #7a7a7a;
    --white: #ffffff;
    --device-light: #e9eaec;
    --device-dark: #9ea3a9;
  }
  html, body {
    margin: 0;
    padding: 0;
    overflow: hidden;
    background: var(--white);
  }
  .slide {
    position: relative;
    width: 1200px;
    height: 675px;
    overflow: hidden;
    background: var(--white);
    font-family: "Open Sans", Arial, sans-serif;
  }
  .side-panel {
    position: absolute;
    inset: 0;
  }
  .slide-title {
    position: absolute;
    left: 47px;
    top: 124px;
    margin: 0;
    font-size: 38px;
    font-weight: 400;
    color: var(--orange);
    letter-spacing: 0.2px;
    white-space: nowrap;
  }
  .intro {
    position: absolute;
    left: 47px;
    top: 187px;
    width: 540px;
    margin: 0;
    font-size: 16.5px;
    line-height: 24px;
    color: var(--text-gray);
    letter-spacing: 0.5px;
  }
  .services {
    position: absolute;
    left: 47px;
    top: 350px;
    margin: 0;
    padding: 0;
    list-style: none;
  }
  .services li {
    position: relative;
    padding-left: 28px;
    height: 36px;
    font-size: 16.5px;
    line-height: 26px;
    color: var(--text-gray);
    letter-spacing: 0.5px;
    white-space: nowrap;
  }
  .services li::before {
    content: "";
    position: absolute;
    left: 3px;
    top: 11px;
    width: 5px;
    height: 5px;
    border-radius: 50%;
    background: var(--orange);
  }
  .dashboard-visual {
    position: absolute;
    left: 668px;
    top: 91px;
    width: 434px;
    height: 462px;
    border-radius: 10px;
    background: linear-gradient(160deg, var(--device-light) 0%, #d6d9dd 55%, var(--device-dark) 100%);
  }
</style>
</head>
<body>
  <div class="slide">
    <svg class="side-panel" width="1200" height="675" viewBox="0 0 1200 675" aria-hidden="true">
      <defs>
        <linearGradient id="panelFade" x1="0" y1="0" x2="1" y2="0">
          <stop offset="0" stop-color="#f4f4f4"/>
          <stop offset="1" stop-color="#fafafa"/>
        </linearGradient>
      </defs>
      <polygon points="0,0 600,0 412,675 0,675" fill="url(#panelFade)"/>
    </svg>

    <h1 class="slide-title">Professionelles IT Management</h1>

    <p class="intro">IT Management bedeutet für uns nicht Reaktion sondern Prävention! Damit erreichen wir eine Hochverfügbarkeit der Server und Endgeräte bei unseren Kunden. Unser Management Umfasst folgende Leistungen.</p>

    <ul class="services">
      <li>Geräte-Monitoring</li>
      <li>Patchmanagement für Norvix Updates</li>
      <li>Internet Content Filter (z.B. Adult Pages, Social Networks, usw.)</li>
      <li>Automatisierte Wartungsarbeiten an Server und Clients</li>
      <li>Monatliches IT Reporting an unsere Kunden</li>
    </ul>

    <div class="dashboard-visual" role="img" aria-label="Foto eines Desktop-Monitors mit einem IT-Management-Dashboard auf dem Bildschirm"></div>
  </div>
</body>
</html>
```